Business Card Design needed - Something Awesome!

Need a business card designed. Company is "Marlowe Advisory" we do consulting and also have sales automation technology.
I'm going to use thick stock or metal, something really nice... I was thinking about a QR Code on the back that would just upload my contact info to the persons contact, etc -

This is a Strategy Company with a tech feel. I'm open to ideas but really want this to be nice!

I need a template that should include:

Name | Position or Title
D: 415.902.3376
www.marloweadvisory.example

I'm going to attach my contact so you can use that one, I need to get this printed.

Target Market(s)

Small to mid size customers, Entrepreneurs etc.

Industry/Entity Type

Consulting, Tech, Private Equity.

Contact Information for Business Card

Name, Phone, Maybe email, URL

Font styles to use
Sans Serif

Colors

Designer to choose only greyscale colors for use in the design.

Requirements
Must have
• Fresh, Clean, stand out from the crowd - will be on thick stock or metal.
Nice to have
• Clean, simple yet impactful.
Should not have
• Not cartoonish

```html
<!DOCTYPE html>
<html lang="en">
<head>
<meta charset="utf-8">
<title>Marlowe Advisory — Business Card</title>
<link rel="stylesheet" href="https://fonts.googleapis.com/css2?family=Roboto:wght@300;400;700&display=swap">
<style>
  :root {
    --backdrop: #3a3a3a;
    --card: #141414;
    --card-edge: #0c0c0c;
    --silver: #d9d9d9;
    --silver-dark: #8d8d8d;
    --text-soft: #9a9a9a;
    --rule: #6f6f6f;
  }
  * { box-sizing: border-box; margin: 0; padding: 0; }
  html, body { width: 1200px; height: 801px; overflow: hidden; }
  body {
    background: var(--backdrop);
    font-family: "Roboto", Arial, sans-serif;
    position: relative;
  }
  .card {
    position: absolute;
    top: 245px;
    width: 540px;
    height: 310px;
    background: var(--card);
    border: 1px solid var(--card-edge);
    overflow: hidden;
  }
  .card--front { left: 40px; }
  .card--back { left: 620px; }

  .wordmark {
    position: absolute;
    right: 40px;
    top: 38px;
    font-weight: 300;
    font-size: 44px;
    letter-spacing: 4px;
    color: var(--silver);
  }
  .divider {
    position: absolute;
    left: 40px;
    right: 40px;
    top: 128px;
    height: 1px;
    background: var(--rule);
  }
  .identity {
    position: absolute;
    left: 40px;
    top: 168px;
  }
  .identity__name {
    font-weight: 700;
    font-size: 19px;
    letter-spacing: 0.5px;
    color: var(--silver-dark);
    text-transform: uppercase;
  }
  .identity__title {
    margin-top: 4px;
    font-size: 14px;
    color: var(--text-soft);
  }
  .identity__rule {
    width: 190px;
    height: 1px;
    background: var(--rule);
    margin: 12px 0 10px;
  }
  .contact {
    list-style: none;
    font-size: 14px;
    color: var(--text-soft);
  }
  .contact li {
    display: flex;
    align-items: center;
    gap: 7px;
    line-height: 22px;
  }
  .contact svg { width: 11px; height: 11px; fill: var(--silver); }
  .web {
    position: absolute;
    right: 40px;
    bottom: 58px;
    font-size: 13px;
    color: var(--text-soft);
    text-align: right;
  }
  .accent-bar {
    position: absolute;
    right: 0;
    bottom: 38px;
    width: 200px;
    height: 10px;
    background: linear-gradient(90deg, var(--silver-dark), #f2f2f2 55%, var(--silver-dark));
  }

  .pattern-field {
    position: absolute;
    inset: 0;
    background: linear-gradient(120deg, #050505 0%, #141414 45%, #2a2a2a 100%);
  }
  .back-mark {
    position: absolute;
    left: 50%;
    top: 50%;
    width: 54px;
    height: 54px;
    transform: translate(-50%, -50%);
    background: linear-gradient(135deg, #ffffff, var(--silver-dark));
  }
</style>
</head>
<body>
  <section class="card card--front" aria-label="Business card front">
    <div class="wordmark">MARLOWE</div>
    <div class="divider"></div>
    <div class="identity">
      <div class="identity__name">Elliot R. Vance</div>
      <div class="identity__title">Founder / CEO</div>
      <div class="identity__rule"></div>
      <ul class="contact">
        <li>
          <svg viewBox="0 0 24 24" aria-hidden="true"><path d="M6.6 10.8a15 15 0 0 0 6.6 6.6l2.2-2.2a1 1 0 0 1 1-.25 11.4 11.4 0 0 0 3.6.57 1 1 0 0 1 1 1V20a1 1 0 0 1-1 1A17 17 0 0 1 3 4a1 1 0 0 1 1-1h3.5a1 1 0 0 1 1 1c0 1.25.2 2.45.57 3.6a1 1 0 0 1-.25 1z"/></svg>
          415.902.3376
        </li>
        <li>
          <svg viewBox="0 0 24 24" aria-hidden="true"><path d="M2 5h20v14H2z M2 5l10 8 10-8" /></svg>
          info@marloweadvisory.example
        </li>
      </ul>
    </div>
    <div class="web">www.marloweadvisory.example</div>
    <div class="accent-bar"></div>
  </section>

  <section class="card card--back" aria-label="Business card back">
    <div class="pattern-field" role="img" aria-label="Tonal pattern of scattered black and charcoal squares in gloss and matte finish"></div>
    <div class="back-mark" aria-hidden="true"></div>
  </section>
</body>
</html>
```